Redesign of business card for Cedar Ridge Mechanical

We are looking for a new design for our business cards for Cedar Ridge Mechanical. We are a plumbing & HVAC construction company, operating on the West Coast of Canada and USA. Logo attached.
Industry/Entity Type
Construction - Plumbing & HVAC
Contact Information for Business Card
Name, address, phone numbers, email, website address
Look and feel
Each slider illustrates characteristics of the customer's brand and the style your logo design should communicate.

```html
<!DOCTYPE html>
<html lang="en">
<head>
<meta charset="utf-8">
<title>Cedar Ridge Mechanical — Business Card</title>
<link href="https://fonts.googleapis.com/css2?family=Montserrat:wght@400;500;700&display=swap" rel="stylesheet">
<style>
  :root {
    --bg: #e6e6e6;
    --card-white: #ffffff;
    --card-black: #161616;
    --ink: #1a1a1a;
    --ink-soft: #555555;
    --ink-muted: #7a7a7a;
    --swoosh: #9a9a9a;
    --rule: #b5b5b5;
  }
  * { margin: 0; padding: 0; box-sizing: border-box; }
  html, body { width: 1200px; height: 801px; overflow: hidden; }
  body {
    background: var(--bg);
    font-family: "Montserrat", sans-serif;
    display: flex;
    align-items: center;
    justify-content: center;
    gap: 60px;
  }
  .card {
    position: relative;
    width: 500px;
    height: 286px;
    border-radius: 18px;
    overflow: hidden;
    box-shadow: 0 8px 24px rgba(0,0,0,0.18);
  }
  .card--front { background: var(--card-white); color: var(--ink); }
  .card--back { background: var(--card-black); }

  .front__swoosh { position: absolute; left: 0; bottom: 0; width: 100%; height: 62px; }

  .brand {
    position: absolute;
    top: 44px;
    left: 0;
    right: 0;
    display: flex;
    align-items: center;
    justify-content: center;
    gap: 12px;
  }
  .brand__mark { width: 22px; height: 22px; background: var(--ink); }
  .brand__name {
    font-weight: 700;
    font-size: 22px;
    letter-spacing: 0.04em;
    text-transform: uppercase;
    color: var(--ink);
  }

  .details {
    position: absolute;
    top: 112px;
    left: 40px;
    right: 30px;
    display: flex;
    align-items: center;
  }
  .person { width: 190px; text-align: right; padding-right: 18px; }
  .person__name { font-size: 17px; font-weight: 700; letter-spacing: 0.04em; text-transform: uppercase; }
  .person__name span { color: var(--ink-soft); }
  .person__role { font-size: 12px; font-weight: 500; margin-top: 3px; }
  .divider { width: 1px; height: 62px; background: var(--rule); }
  .contact { list-style: none; padding-left: 18px; font-size: 13px; color: var(--ink-soft); }
  .contact li { display: flex; align-items: center; gap: 7px; line-height: 21px; }
  .contact svg { width: 11px; height: 11px; fill: var(--ink); flex: none; }

  .address {
    position: absolute;
    top: 192px;
    left: 0; right: 0;
    text-align: center;
    font-size: 13px;
    color: var(--ink-muted);
  }

  .back__pattern {
    position: absolute;
    inset: 0;
    background: linear-gradient(135deg, #1c1c1c 0%, #262626 50%, #121212 100%);
  }
  .back__brand {
    position: absolute;
    inset: 0;
    display: flex;
    align-items: center;
    justify-content: center;
    gap: 10px;
  }
  .back__brand .brand__mark { width: 18px; height: 18px; background: #ffffff; }
  .back__brand .brand__name { color: #ffffff; font-size: 18px; }
</style>
</head>
<body>
  <section class="card card--front">
    <div class="brand">
      <span class="brand__mark"></span>
      <span class="brand__name">Cedar Ridge Mechanical</span>
    </div>

    <div class="details">
      <div class="person">
        <div class="person__name">Daniel <span>Harper</span></div>
        <div class="person__role">Manager</div>
      </div>
      <div class="divider"></div>
      <ul class="contact">
        <li><svg viewBox="0 0 24 24"><path d="M6.6 10.8a15.5 15.5 0 0 0 6.6 6.6l2.2-2.2c.3-.3.7-.4 1-.2 1.1.4 2.3.6 3.6.6.6 0 1 .4 1 1V20c0 .6-.4 1-1 1A17 17 0 0 1 3 4c0-.6.4-1 1-1h3.5c.6 0 1 .4 1 1 0 1.3.2 2.5.6 3.6.1.3 0 .7-.2 1z"/></svg>555-018-2743</li>
        <li><svg viewBox="0 0 24 24"><path d="M2 5h20v14H2z M4 7v1l8 5 8-5V7l-8 5z"/></svg>youremail@mailbox.com</li>
        <li><svg viewBox="0 0 24 24"><circle cx="12" cy="12" r="10"/></svg>www.yourwebsite.com</li>
      </ul>
    </div>

    <div class="address">Your address, city, state, ZIP 0000</div>

    <svg class="front__swoosh" viewBox="0 0 500 62" preserveAspectRatio="none" aria-hidden="true">
      <path d="M0 62 L0 42 Q260 62 500 0 L500 62 Z" fill="var(--swoosh)"/>
      <path d="M0 62 L0 48 Q260 68 500 8 L500 62 Z" fill="var(--ink)"/>
    </svg>
  </section>

  <section class="card card--back">
    <div class="back__pattern" role="img" aria-label="Repeating glossy spot-varnish pattern of the company mark on black"></div>
    <div class="back__brand">
      <span class="brand__mark"></span>
      <span class="brand__name">Cedar Ridge Mechanical</span>
    </div>
  </section>
</body>
</html>
```